Willow Fen Racquet Club (Tennis Country Club)

Racquet and Tennis Country Club in Florida.
This web sight is needed for a Privet Tennis club located in Deerfield Beach city in Florida, USA.
We have 10 clay tennis courts and 2 hard tennis courts, small and cozy swimming pool and a clubhouse (see attached pictures) Attached pictures are for information only because we are under a reconstruction.
Updates

I haven't received any source files and web converted files neither!

Target Market(s)

Adult members, Kids members, Tennis players

Coding

Coded - Design and coding required

Number of Pages Required

3 page

Requirements
Must have
• Logo colors (see attached file)

```html
<!DOCTYPE html>
<html lang="en">
<head>
<meta charset="utf-8">
<title>Willow Fen Racquet Club</title>
<link rel="stylesheet" href="https://fonts.googleapis.com/css2?family=PT+Sans:wght@400;700&family=Open+Sans:wght@400;600;700&display=swap">
<style>
:root{
  --green-dark:#1d6b3a;
  --green:#4fa33a;
  --green-light:#7cc34a;
  --ink:#3d3d3d;
  --muted:#6b6b6b;
  --mist:#e8efeb;
  --white:#ffffff;
}
*{box-sizing:border-box;margin:0;padding:0}
html,body{width:1200px;height:3303px;overflow:hidden}
body{position:relative;background:var(--white);font-family:"Open Sans",sans-serif;color:var(--ink)}
.abs{position:absolute}
.heading{font-family:"PT Sans",sans-serif;font-weight:700}

/* header */
.brand{left:88px;top:32px;width:180px;text-align:center}
.brand-name{font-family:"PT Sans",sans-serif;font-weight:700;font-size:26px;color:#333;line-height:1.2;white-space:nowrap}
.call{left:738px;top:26px;font-size:17px;color:#333}
.call b{color:var(--green-dark)}
.btn-schedule{left:990px;top:20px;width:110px;height:40px;background:var(--green-dark);color:var(--white);font-weight:700;font-size:15px;display:flex;align-items:center;justify-content:center}
.nav{right:100px;top:77px;display:flex;gap:26px;font-size:14px;color:#222;font-weight:600}
.nav .active{color:var(--green-dark);font-weight:700}

/* hero */
.hero{left:0;top:112px;width:1200px;height:584px;background:linear-gradient(100deg,#c9dc6a 0%,#a9c843 25%,#6f9a2f 55%,#7fa73a 80%,#9fbe52 100%)}
.hero-kicker{left:620px;top:238px;font-size:20px;font-weight:700;color:var(--white)}
.hero-title{left:616px;top:268px;font-size:72px;color:var(--white);line-height:1}
.hero-sub{left:620px;top:356px;font-size:22px;font-weight:700;color:var(--white);line-height:1.5;width:500px}
.btn-hero{left:621px;top:440px;width:152px;height:53px;background:var(--green-dark);border:2px solid var(--white);color:var(--white);font-size:19px;display:flex;align-items:center;justify-content:center}
.dots{left:575px;top:583px;display:flex;gap:5px}
.dots i{width:10px;height:10px;border-radius:50%;border:1.5px solid var(--white);display:block}
.dots i.on{background:var(--white)}
.wave{left:0;width:1200px}

/* about */
.section-title{left:0;width:1200px;text-align:center;font-size:37px;color:#3a3a3a}
.about-text{left:183px;top:822px;width:836px;text-align:center;font-size:12.5px;line-height:28px;color:#555}
.btn-outline{border:2px solid var(--green-dark);color:var(--green-dark);font-weight:700;font-size:15px;display:flex;align-items:center;justify-content:center;background:var(--white)}
.racket{left:968px;top:916px;width:232px;height:190px;background:linear-gradient(150deg,#f4f6ec 0%,#d8e48a 55%,#c4d83e 100%)}

/* features */
.band-green{left:0;top:1244px;width:1200px;height:345px;background:linear-gradient(180deg,var(--green-light),var(--green))}
.feature-label{font-size:20px;color:var(--green-dark);text-align:center;width:320px}
.feature-photo{border:4px solid var(--white);box-shadow:0 2px 6px rgba(0,0,0,.25)}
.feature-text{font-size:12px;line-height:20px;color:var(--white);text-align:center}
.btn-pill{width:126px;height:38px;border:2px solid var(--white);border-radius:20px;background:var(--green);color:var(--white);font-size:12px;font-weight:700;display:flex;align-items:center;justify-content:center;gap:6px;box-shadow:0 2px 4px rgba(0,0,0,.2)}

/* events */
.kicker{left:0;width:1200px;text-align:center;font-size:15px;font-weight:700;color:#555}
.event{top:1755px;width:233px;height:320px;background:var(--white);box-shadow:0 3px 10px rgba(0,0,0,.15)}
.event-photo{width:233px;height:178px}
.event-meta{margin:20px 0 0 12px;font-size:12px;color:#333;display:flex;align-items:center;gap:6px}
.event-meta svg{flex:none}
.event-title{margin:18px 12px 0 12px;font-size:14.5px;line-height:26px;color:#666}

/* quotation */
.quote{left:0;top:2206px;width:1200px;height:480px;background:linear-gradient(180deg,var(--green-light),var(--green))}
.quote-title{left:99px;top:2282px;font-size:34px;color:var(--white)}
.field{border:2px solid var(--white);color:var(--white);font-size:11px;padding-left:14px;display:flex;align-items:center}
.btn-submit{left:99px;top:2503px;width:94px;height:40px;background:var(--green-dark);border:2px solid var(--white);color:var(--white);font-weight:700;font-size:15px;display:flex;align-items:center;justify-content:center}
.player{left:690px;top:2213px;width:510px;height:462px;background:linear-gradient(160deg,#5c8a2f 0%,#a8d98c 45%,#8ccf6e 70%,#5aa636 100%)}

/* clients */
.clients{left:0;top:2620px;width:1200px;height:342px;background:var(--mist)}
.client{top:2805px;height:76px;background:var(--white);box-shadow:0 2px 8px rgba(0,0,0,.15);display:flex;align-items:center;justify-content:center;gap:8px;font-family:"PT Sans",sans-serif;font-weight:700;font-size:20px;color:#555}
.client i{width:12px;height:12px;background:#777;display:block}

/* footer */
.f-brand{left:84px;top:3108px;width:180px;text-align:center}
.f-head{font-size:16px;font-weight:700;color:var(--green-dark);font-family:"PT Sans",sans-serif}
.f-links{list-style:none;font-size:11.5px;color:#444;line-height:23px}
.f-links li::before{content:"» ";color:#666}
.f-addr{font-size:11.5px;color:#444;line-height:23px}
.f-row{display:flex;gap:10px;align-items:flex-start}
.f-row svg{margin-top:6px;flex:none}
.news-input{left:806px;top:3063px;width:295px;height:40px;border:1px solid #bbb;font-size:12px;color:#666;padding-left:16px;display:flex;align-items:center}
.btn-sub{left:810px;top:3120px;width:110px;height:40px;background:var(--green-dark);color:var(--white);font-weight:700;font-size:14px;display:flex;align-items:center;justify-content:center}
.rule{left:99px;top:3245px;width:1002px;height:1px;background:#aaa}
.legal{top:3268px;font-size:11.5px;color:#555}
</style>
</head>
<body>

<!-- Header -->
<div class="abs brand"><div class="brand-name">Willow Fen</div></div>
<div class="abs call"><b>Call Us -</b> (+1)555-014-2290</div>
<div class="abs btn-schedule">Schedule</div>
<nav class="abs nav">
  <span class="active">Home</span><span>About</span><span>Club</span><span>Programs</span><span>Membership</span><span>Events</span><span>Contact</span>
</nav>

<!-- Hero -->
<div class="abs hero" role="img" aria-label="Tennis ball resting against a net on a grass court"></div>
<div class="abs hero-kicker">Tennis Club In Florida</div>
<h1 class="abs hero-title heading">Willow Fen</h1>
<p class="abs hero-sub">Lorem Ipsum is simply dummy text of printing and typesetting industry.</p>
<div class="abs btn-hero">Read More</div>
<div class="abs dots"><i class="on"></i><i></i><i></i><i></i></div>
<svg class="abs wave" style="top:600px" width="1200" height="100" viewBox="0 0 1200 100" preserveAspectRatio="none">
  <path d="M0 100 L0 70 C260 0 560 -10 760 30 C930 62 1080 70 1200 60 L1200 100 Z" fill="#fff"/>
</svg>

<!-- About -->
<h2 class="abs section-title heading" style="top:752px">About Willow Fen</h2>
<p class="abs about-text">Lorem Ipsum is simply dummy text of the printing and typesetting industry. Lorem Ipsum has been the industry's standard dummy text ever since the 1500s, when an unknown printer took a galley of type and scrambled it to make a type specimen book. It has survived not only five centuries, but also the leap into electronic typesetting, remaining essentially unchanged. It was popularised in the 1960s with the release of Letraset sheets containing Lorem Ipsum passages with desktop publishing software</p>
<div class="abs btn-outline" style="left:493px;top:973px;width:214px;height:48px">Read More Information</div>
<div class="abs racket" role="img" aria-label="Tennis racket with three tennis balls"></div>

<!-- Features -->
<div class="abs band-green"></div>
<svg class="abs wave" style="top:1540px" width="1200" height="60" viewBox="0 0 1200 60" preserveAspectRatio="none">
  <path d="M0 0 L0 40 C300 0 700 -10 1200 40 L1200 60 L0 60 Z" fill="#fff"/>
</svg>

<div class="abs feature-label heading" style="left:100px;top:1154px">PLAY TENNIS</div>
<div class="abs feature-photo" style="left:103px;top:1191px;width:316px;height:193px;background:linear-gradient(180deg,#7da7d6 0%,#b5cfe8 45%,#5c7a8a 60%,#3f6b8f 100%)" role="img" aria-label="Outdoor tennis courts under a blue sky"></div>
<p class="abs feature-text" style="left:103px;top:1404px;width:316px">Lorem Ipsum is simply dummy text of the printing. It is tLorem Ipsum has been the industry's standard</p>
<div class="abs btn-pill" style="left:198px;top:1453px">› Read More</div>

<div class="abs feature-label heading" style="left:443px;top:1119px">GET WET</div>
<div class="abs feature-photo" style="left:443px;top:1156px;width:322px;height:195px;background:linear-gradient(180deg,#d9dde0 0%,#9fb2bf 25%,#2b8ee0 45%,#1f7fd3 100%)" role="img" aria-label="Clubhouse swimming pool"></div>
<p class="abs feature-text" style="left:443px;top:1370px;width:322px">Lorem Ipsum is simply dummy text of the printing and typesetting industry. Lorem Ipsum has been the indus try's standard dummy text ever since the 1500s, when an unknown printer took a galley of type</p>

<div class="abs feature-label heading" style="left:782px;top:1154px">CLUB HOUSE</div>
<div class="abs feature-photo" style="left:784px;top:1191px;width:316px;height:193px;background:linear-gradient(180deg,#3f86d1 0%,#e9eef2 35%,#c7d2d8 60%,#2a9be2 100%)" role="img" aria-label="Clubhouse terrace beside the pool"></div>
<p class="abs feature-text" style="left:784px;top:1404px;width:316px">Lorem Ipsum is simply dummy text of the printing. It is tLorem Ipsum has been the industry's standard</p>
<div class="abs btn-pill" style="left:879px;top:1453px">› Read More</div>

<!-- Events -->
<div class="abs kicker" style="top:1651px">News &amp; Articles</div>
<h2 class="abs section-title heading" style="top:1674px">Upcoming Events</h2>

<div class="abs event" style="left:101px">
  <div class="event-photo" role="img" aria-label="Tennis balls on a racket on grass" style="background:linear-gradient(160deg,#f2f2f2 0%,#c9df52 45%,#6aa23a 100%)"></div>
  <div class="event-meta"><svg width="11" height="11" viewBox="0 0 11 11"><rect x="0.5" y="1.5" width="10" height="9" fill="none" stroke="#333"/><rect x="0.5" y="1.5" width="10" height="3" fill="#333"/></svg>April 28, 2018 &nbsp;|&nbsp; <svg width="10" height="11" viewBox="0 0 10 11"><circle cx="5" cy="3" r="2.6" fill="#333"/><path d="M0 11 C0 6 10 6 10 11 Z" fill="#333"/></svg>Sam Reyes</div>
  <div class="event-title">Lorem Ipsum Is Simply Dummy Text of Printing</div>
</div>
<div class="abs event" style="left:356px">
  <div class="event-photo" role="img" aria-label="Player on a padel court" style="background:linear-gradient(180deg,#c8d4de 0%,#8da0ad 45%,#4d7a8f 100%)"></div>
  <div class="event-meta"><svg width="11" height="11" viewBox="0 0 11 11"><rect x="0.5" y="1.5" width="10" height="9" fill="none" stroke="#333"/><rect x="0.5" y="1.5" width="10" height="3" fill="#333"/></svg>April 28, 2018 &nbsp;|&nbsp; <svg width="10" height="11" viewBox="0 0 10 11"><circle cx="5" cy="3" r="2.6" fill="#333"/><path d="M0 11 C0 6 10 6 10 11 Z" fill="#333"/></svg>Sam Reyes</div>
  <div class="event-title">Lorem Ipsum Is Simply Dummy Text of Printing</div>
</div>
<div class="abs event" style="left:610px">
  <div class="event-photo" role="img" aria-label="Tennis ball on a court line" style="background:linear-gradient(160deg,#e3ecd8 0%,#5f9a45 45%,#2f6e35 100%)"></div>
  <div class="event-meta"><svg width="11" height="11" viewBox="0 0 11 11"><rect x="0.5" y="1.5" width="10" height="9" fill="none" stroke="#333"/><rect x="0.5" y="1.5" width="10" height="3" fill="#333"/></svg>April 28, 2018 &nbsp;|&nbsp; <svg width="10" height="11" viewBox="0 0 10 11"><circle cx="5" cy="3" r="2.6" fill="#333"/><path d="M0 11 C0 6 10 6 10 11 Z" fill="#333"/></svg>Sam Reyes</div>
  <div class="event-title">Lorem Ipsum Is Simply Dummy Text of Printing</div>
</div>
<div class="abs event" style="left:863px">
  <div class="event-photo" role="img" aria-label="Player serving against a blue sky" style="background:linear-gradient(180deg,#5a8fd6 0%,#8db3e6 60%,#c7d9f0 100%)"></div>
  <div class="event-meta"><svg width="11" height="11" viewBox="0 0 11 11"><rect x="0.5" y="1.5" width="10" height="9" fill="none" stroke="#333"/><rect x="0.5" y="1.5" width="10" height="3" fill="#333"/></svg>April 28, 2018 &nbsp;|&nbsp; <svg width="10" height="11" viewBox="0 0 10 11"><circle cx="5" cy="3" r="2.6" fill="#333"/><path d="M0 11 C0 6 10 6 10 11 Z" fill="#333"/></svg>Sam Reyes</div>
  <div class="event-title">Lorem Ipsum Is Simply Dummy Text of Printing</div>
</div>

<!-- Quotation -->
<div class="abs clients"></div>
<div class="abs quote"></div>
<div class="abs player" role="img" aria-label="Tennis player serving in a green shirt"></div>
<svg class="abs wave" style="top:2610px" width="1200" height="80" viewBox="0 0 1200 80" preserveAspectRatio="none">
  <path d="M0 80 L0 40 C250 -5 520 0 760 30 C950 55 1080 60 1200 55 L1200 80 Z" fill="#e8efeb"/>
</svg>
<h2 class="abs quote-title heading">Get A Quotation</h2>
<div class="abs field" style="left:99px;top:2354px;width:232px;height:45px">Name</div>
<div class="abs field" style="left:359px;top:2354px;width:232px;height:45px">Phone</div>
<div class="abs field" style="left:99px;top:2431px;width:492px;height:45px">Your Message</div>
<div class="abs btn-submit">Submit</div>

<!-- Clients -->
<h2 class="abs section-title heading" style="top:2712px">Our Clients</h2>
<div class="abs client" style="left:174px;width:175px"><i></i>Harbor Loft</div>
<div class="abs client" style="left:398px;width:180px;height:96px;top:2795px">Sunmint</div>
<div class="abs client" style="left:625px;width:177px"><i></i>Millworks</div>
<div class="abs client" style="left:852px;width:177px">Grand Oak</div>

<!-- Footer -->
<div class="abs f-brand"><div class="brand-name">Willow Fen</div></div>
<div class="abs" style="left:350px;top:3022px">
  <div class="f-head">Quick Links</div>
  <ul class="f-links" style="margin-top:8px">
    <li>Home</li><li>About</li><li>Club</li><li>Programs</li><li>Membership</li><li>Events</li><li>Contact</li>
  </ul>
</div>
<div class="abs" style="left:539px;top:3022px">
  <div class="f-head">Address</div>
  <div class="f-addr" style="margin-top:8px">
    <div class="f-row"><svg width="9" height="12" viewBox="0 0 9 12"><path d="M4.5 0 C2 0 0 2 0 4.5 C0 7.5 4.5 12 4.5 12 C4.5 12 9 7.5 9 4.5 C9 2 7 0 4.5 0 Z" fill="#1d6b3a"/><circle cx="4.5" cy="4.5" r="1.6" fill="#fff"/></svg><span>Willow Fen Tennis Club,<br>Lorem Ipsum is Simple,<br>Lorem Ipsum</span></div>
    <div class="f-row"><svg width="10" height="10" viewBox="0 0 10 10"><path d="M2 0 L4 2.5 L3 4 C4 6 5 7 6.5 7.5 L8 6.5 L10 8.5 L8.5 10 C4 9.5 0.5 6 0 1.5 Z" fill="#1d6b3a"/></svg><span>(+1)555-014-2290</span></div>
    <div class="f-row"><svg width="11" height="9" viewBox="0 0 11 9"><rect width="11" height="9" fill="#1d6b3a"/><path d="M0 0 L5.5 5 L11 0" fill="none" stroke="#fff" stroke-width="1"/></svg><span>hello@willowfenclub.com</span></div>
  </div>
</div>
<div class="abs f-head" style="left:801px;top:3022px">Subscribe To Newsletter</div>
<div class="abs news-input">Enter your Email</div>
<div class="abs btn-sub">Subscribe</div>
<div class="abs rule"></div>
<div class="abs legal" style="left:103px">Copyright 2018 &nbsp;All Rights Reserved.</div>
<div class="abs legal" style="left:932px">Terms of Use &nbsp;|&nbsp; Privacy Policy</div>

</body>
</html>
```